Brightfen Business Card Redesign & Logo Update

We need to update our business cards to something more modern and fresh. Brightfen can provide the current color schemes and old design examples, but welcome creativity in helping us with this redesign. PLEASE NOTE that we no longer utilize the "tree" and/or "leaf" imagery in our branding. If able would apprecaite an update on the quality of our "words only" logo in Ai. / PNG formats too.

Target Market(s)

Investors, landowners, corporate partners, contractors

Industry/Entity Type

Environmental Restoration & Conservation

Contact Information for Business Card

Logo, persons name, title, mailing address, phone and email, website url

Font styles to use
Other font styles liked:
• Merriweather

Requirements
Nice to have
• Logo, persons name, title, mailing address, phone and email, website url, but open to ideams
Should not have
• No all back backgrounds

```html
<!DOCTYPE html>
<html lang="en">
<head>
<meta charset="utf-8">
<title>Brightfen Business Card</title>
<link href="https://fonts.googleapis.com/css2?family=Oswald:wght@500;700&family=Open+Sans:wght@400;600;700&display=swap" rel="stylesheet">
<style>
  :root {
    --page: #d6d6d8;
    --card: #44474e;
    --card-deep: #383b41;
    --edge: #ef7f22;
    --orange: #ef7f22;
    --green: #2fae5c;
    --white: #ffffff;
  }
  * { box-sizing: border-box; margin: 0; padding: 0; }
  html, body { width: 1200px; height: 780px; overflow: hidden; }
  body { background: var(--page); position: relative; font-family: "Open Sans", sans-serif; }

  .card {
    position: absolute;
    top: 90px;
    width: 340px;
    height: 600px;
    background: linear-gradient(160deg, var(--card) 0%, var(--card-deep) 100%);
    border-radius: 30px;
    box-shadow: 0 5px 0 var(--edge), 0 14px 26px rgba(0,0,0,.3);
    overflow: hidden;
  }
  .card--front { left: 220px; }
  .card--back { left: 640px; }

  /* front */
  .front-mark {
    position: absolute;
    left: 50%;
    top: 50%;
    width: 540px;
    transform: translate(-50%, -50%) rotate(-90deg);
    text-align: center;
  }
  .wordmark {
    font-family: "Oswald", sans-serif;
    font-weight: 700;
    color: var(--orange);
    text-transform: uppercase;
    line-height: 1;
  }
  .front-mark .wordmark { font-size: 112px; letter-spacing: 2px; }
  .tagline {
    font-family: "Oswald", sans-serif;
    font-weight: 500;
    color: var(--white);
    text-transform: uppercase;
    line-height: 1;
  }
  .front-mark .tagline { font-size: 31px; letter-spacing: 0.5px; margin-top: 8px; }

  /* back */
  .back-logo { position: absolute; top: 58px; left: 0; width: 100%; text-align: center; }
  .back-logo .wordmark { font-size: 62px; letter-spacing: 1px; }
  .back-logo .tagline { font-size: 16.5px; margin-top: 4px; letter-spacing: 0.3px; }

  .person { position: absolute; top: 372px; left: 0; width: 100%; text-align: center; }
  .person__name { font-size: 23px; font-weight: 700; color: var(--orange); }
  .person__name .surname { color: var(--green); }
  .person__title { font-size: 15px; color: var(--white); margin-top: 2px; }

  .contact-rule { position: absolute; top: 432px; left: 0; width: 340px; height: 40px; }

  .contact-list { position: absolute; top: 482px; left: 0; width: 100%; list-style: none; text-align: center; }
  .contact-list li { font-size: 13.5px; color: var(--white); line-height: 1.5; letter-spacing: 0.2px; }
</style>
</head>
<body>

  <section class="card card--front" aria-label="Card front">
    <div class="front-mark">
      <div class="wordmark">Brightfen</div>
      <div class="tagline">Environmental Credit Company</div>
    </div>
  </section>

  <section class="card card--back" aria-label="Card back">
    <header class="back-logo">
      <div class="wordmark">Brightfen</div>
      <div class="tagline">Environmental Credit Company</div>
    </header>

    <div class="person">
      <p class="person__name">Lenka <span class="surname">Moravcova</span></p>
      <p class="person__title">Co-Founder</p>
    </div>

    <svg class="contact-rule" viewBox="0 0 340 40" aria-hidden="true">
      <g fill="#ef7f22">
        <circle cx="14" cy="20" r="2.5"/>
        <circle cx="28" cy="20" r="3.5"/>
        <circle cx="44" cy="20" r="4.5"/>
        <circle cx="62" cy="20" r="5.5"/>
        <circle cx="82" cy="20" r="6.5"/>
        <circle cx="104" cy="20" r="7.5"/>
        <circle cx="236" cy="20" r="7.5"/>
        <circle cx="258" cy="20" r="6.5"/>
        <circle cx="278" cy="20" r="5.5"/>
        <circle cx="296" cy="20" r="4.5"/>
        <circle cx="312" cy="20" r="3.5"/>
        <circle cx="326" cy="20" r="2.5"/>
        <circle cx="136" cy="20" r="15"/>
        <circle cx="170" cy="20" r="15"/>
        <circle cx="204" cy="20" r="15"/>
      </g>
      <g fill="none" stroke="#ffffff" stroke-width="1.6" stroke-linecap="round" stroke-linejoin="round">
        <path d="M130 13 q-2 2 0 6 q3 6 9 9 q3 1 5 -1 l-3 -3 l-2 1 q-3 -2 -5 -5 l1 -2 z"/>
        <rect x="162" y="14" width="16" height="12" rx="1.5"/>
        <path d="M162 15 l8 6 l8 -6"/>
        <circle cx="204" cy="20" r="8"/>
        <ellipse cx="204" cy="20" rx="3.5" ry="8"/>
        <path d="M196 20 h16"/>
      </g>
    </svg>

    <ul class="contact-list">
      <li>(555) 214-6083</li>
      <li>hello@brightfen.co</li>
      <li>www.brightfen.co</li>
      <li>410 Marsh Lane, Tulsa, OK 74103</li>
    </ul>
  </section>

</body>
</html>
```